Suds Haven Laundromat Wordpress Design

We need a Wordpress website design for our laundromat, Suds Haven Atlanta, at www.sudshavenatlanta-example.com. We would like to have 6 pages: Home, About Us, Services, Locations, Reviews and Contact us. We will provide content for the text on each page. What we do: We are a full service laundromat that provides dry cleaning drop off, professional laundry services, wash dry fold and self service laundry to the local community. We would like to use the color scheme from our logo to convey a warm, safe, and bright business that caters to its diverse community.
Updates

I like the structure of this laundromat website: http://www.washtroveusa-example.com/ Using my logo and color scheme in the above referenced website is what. Am looking for. The photos attached to the project with the female model should be used as a primary focus and supplemented by actual photos of the equipment.

Target Market(s)

Our target market is a diverse group of people from Midtown Atlanta - LGBTQ community /Locals/Regulars that have been coming to laundromat for 30 years.

Industry/Entity Type

Laundromat

Coding

Coded - Design and coding required

Number of Pages Required

5+ page

Font styles to use
Sans Serif

Colors
0054AA
0677BA
7BADD7
CADEEF
E8F1F8

Requirements
Must have
• Feature this video on the main page: https://videohost-example.com/xq7Rm2bPz4k

```html
<!DOCTYPE html>
<html lang="en">
<head>
<meta charset="utf-8">
<title>Suds Haven Laundromat</title>
<link href="https://fonts.googleapis.com/css2?family=Barlow:wght@600;700&family=Roboto+Condensed:wght@400;700&family=Poppins:wght@400;500&display=swap" rel="stylesheet">
<style>
:root{
  --deep:#0054AA;
  --brand:#0677BA;
  --band:#0a6aa8;
  --sky:#7BADD7;
  --mist:#CADEEF;
  --ice:#E8F1F8;
  --ink:#111;
  --grey:#666;
  --white:#fff;
}
*{margin:0;padding:0;box-sizing:border-box}
html,body{width:1200px;height:3544px;overflow:hidden}
body{position:relative;background:var(--white);font-family:"Poppins",sans-serif;color:var(--ink)}
.abs{position:absolute}
.title{font-family:"Barlow",sans-serif;font-weight:700;color:var(--deep);font-size:29px;text-align:center;width:1200px;left:0}

/* top bar + header */
.topbar{top:0;left:0;width:1200px;height:37px;background:var(--band);color:#fff;font-size:12px}
.topbar .welcome{left:61px;top:11px;line-height:15px}
.topbar .dot{top:11px;width:15px;height:15px;border-radius:50%;background:#fff}
.header{top:37px;left:0;width:1200px;height:73px;background:#fff}
.brand{font-family:"Roboto Condensed",sans-serif;font-weight:700;color:var(--deep);font-size:27px;line-height:32px;left:59px;top:58px;display:flex;align-items:center;gap:8px}
.brand i{display:block;width:12px;height:12px;border-radius:50%;background:var(--sky)}
.nav{top:66px;font-family:"Roboto Condensed",sans-serif;font-size:13px;line-height:16px;color:#444}
.nav.active{color:var(--brand)}
.nav-ring{left:384px;top:56px;width:42px;height:38px;border-radius:50%;border:1px solid var(--mist)}
.phone-btn{left:974px;top:52px;width:165px;height:44px;border-radius:22px;background:var(--brand);color:#fff;font-family:"Roboto Condensed",sans-serif;font-weight:700;font-size:16px;display:flex;align-items:center;gap:12px;padding-left:5px}
.phone-btn span.ic{width:36px;height:36px;border-radius:50%;background:#fff;display:flex;align-items:center;justify-content:center}

/* hero */
.hero{top:110px;left:0;width:1200px;height:640px;background:linear-gradient(90deg,#f4f8fb,#eef4f9)}
.hero-arc{left:-260px;top:180px;width:440px;height:380px;border-radius:50%;border:28px solid rgba(202,222,239,.35)}
.hero-title{left:62px;top:314px;font-family:"Roboto Condensed",sans-serif;font-weight:700;font-size:52px;line-height:61px;color:var(--ink);white-space:nowrap}
.hero-title em{font-style:normal;color:var(--deep)}
.offer{left:60px;top:534px;width:188px;height:44px;border-radius:22px;background:var(--brand);color:#fff;font-family:"Roboto Condensed",sans-serif;font-weight:700;font-size:15px;display:flex;align-items:center;gap:16px;padding-left:4px}
.offer b{width:36px;height:36px;border-radius:50%;background:#fff;color:var(--brand);display:flex;align-items:center;justify-content:center;font-size:18px}
.hero-ring{left:532px;top:140px;width:592px;height:592px;border-radius:50% 14px 50% 50%;background:var(--mist);opacity:.7}
.hero-photo{left:546px;top:154px;width:566px;height:566px;border-radius:50% 8px 50% 50%;background:linear-gradient(160deg,#bfe2dc 0%,#9fcfd0 35%,#3d7fc1 65%,#d9dfe4 100%)}

/* what we do */
.feature{width:280px;text-align:center}
.feature .ic{margin:0 auto;width:112px;height:112px;border-radius:50%;background:var(--ice);display:flex;align-items:center;justify-content:center}
.feature .ic.ring{border:2px solid var(--brand);background:#fff;box-shadow:inset 0 0 0 8px var(--ice)}
.feature h3{font-family:"Roboto Condensed",sans-serif;font-weight:700;font-size:16px;margin-top:20px}
.feature p{font-size:12.5px;line-height:19px;color:var(--grey);margin-top:12px;padding:0 30px}

/* services */
.svc-title{color:#fff}
.drop{width:262px;height:262px;background:#fff;transform:rotate(45deg)}
.drop.down{border-radius:0 50% 50% 50%}
.drop.up{border-radius:50% 50% 0 50%}
.drop-body{width:262px;text-align:center}
.drop-body h4{font-family:"Roboto Condensed",sans-serif;font-weight:700;font-size:16px;margin-top:8px}
.drop-body p{font-size:12.5px;line-height:19px;color:var(--grey);padding:0 44px}
.drop-photo{margin:0 auto;width:124px;height:146px;border-radius:50% 50% 50% 50%/58% 58% 42% 42%;background:linear-gradient(160deg,#6f9fd0,#c9d9e8)}
.drop-photo.inv{border-radius:50% 50% 50% 50%/42% 42% 58% 58%;background:linear-gradient(200deg,#e6e9ed,#6a7d92)}

/* testimonial */
.client-photo{left:209px;top:1899px;width:240px;height:262px;border-radius:8px 50% 50% 50%;background:linear-gradient(150deg,#e9e3dc,#d7b6b1 60%,#c9cfd8)}
.quote-card{left:383px;top:1986px;width:598px;height:137px;border-radius:69px;background:var(--ice)}
.quote-badge{left:444px;top:1915px;width:68px;height:110px;border-radius:14px 14px 0 0;background:var(--deep);color:#fff;font-family:Georgia,serif;font-size:82px;line-height:110px;text-align:center}
.quote-text{left:454px;top:2036px;width:380px;font-size:12.5px;line-height:19px;color:#333}
.dots{left:871px;top:2098px;display:flex;gap:5px}
.dots i{width:6px;height:6px;border-radius:50%;background:var(--mist)}
.dots i:first-child{background:var(--brand)}
.model-photo{left:880px;top:1768px;width:224px;height:436px;border-radius:110px 110px 20px 20px;background:linear-gradient(180deg,#f3e2d6 0%,#2f78c4 30%,#1f5fa8 60%,#d6a64a 100%);opacity:.95}

/* video */
.video-title{left:0;width:1200px;text-align:center;font-family:"Roboto Condensed",sans-serif;font-weight:400;font-size:34px;line-height:42px;color:#fff;top:2314px}
.video-text{left:390px;width:420px;text-align:center;top:2414px;font-size:12.5px;line-height:19px;color:#fff}
.play{left:516px;top:2498px;width:74px;height:74px;border-radius:50%;border:2px solid rgba(255,255,255,.6);display:flex;align-items:center;justify-content:center}
.play span{width:56px;height:56px;border-radius:50%;background:rgba(255,255,255,.85);display:flex;align-items:center;justify-content:center}
.watch{left:609px;top:2526px;font-family:"Roboto Condensed",sans-serif;font-weight:700;color:#fff;font-size:15px}

/* about */
.about-title{left:136px;top:2742px;font-family:"Barlow",sans-serif;font-weight:700;color:var(--deep);font-size:29px}
.about-list{left:135px;top:2796px;list-style:none}
.about-list li{height:37.6px;font-size:12.5px;color:#333;display:flex;align-items:center;gap:10px}
.about-list li::before{content:"";width:13px;height:13px;border-radius:50%;border:3px solid var(--brand);box-sizing:border-box}
.about-list li em{font-style:normal;color:var(--brand)}
.more{left:135px;top:3027px;width:127px;height:36px;border-radius:18px;background:var(--brand);color:#fff;font-family:"Roboto Condensed",sans-serif;font-weight:700;font-size:15px;display:flex;align-items:center;justify-content:center}
.pic{width:184px;height:184px;border-radius:50%}
.pic.a{left:680px;top:2724px;background:linear-gradient(150deg,#9aa6b3,#e1a23c 55%,#2d5c8f)}
.pic.b{left:888px;top:2724px;background:linear-gradient(150deg,#d7dde3,#8c7a6e 55%,#e8eaed)}
.pic.c{left:680px;top:2917px;background:linear-gradient(150deg,#f0f2f4,#aeb6bf 60%,#7d8791)}
.pic.d{left:888px;top:2917px;background:linear-gradient(150deg,#e8ebef,#3b3a40 50%,#c9ced6)}

/* footer */
.foot-brand{left:59px;top:3268px;font-family:"Roboto Condensed",sans-serif;font-weight:700;color:#fff;font-size:30px;display:flex;align-items:center;gap:8px}
.foot-brand i{width:14px;height:14px;border-radius:50%;background:var(--mist);display:block}
.foot-social{left:59px;top:3333px;display:flex;gap:6px}
.foot-social i{width:34px;height:34px;border-radius:50%;border:1.5px solid #fff;display:block}
.foot-col h5{font-family:"Roboto Condensed",sans-serif;font-weight:700;font-size:18px;color:#fff;margin-bottom:10px}
.foot-col li{list-style:none;color:#fff;font-size:12px;height:27px}
.contact-row{left:888px;color:#fff;font-size:12.5px;line-height:19px;display:flex;gap:18px;align-items:flex-start}
.copy{left:0;top:3506px;width:1200px;height:38px;background:var(--brand);color:#fff;font-size:12px;text-align:center;line-height:38px}
</style>
</head>
<body>

<svg class="abs" style="left:0;top:0" width="1200" height="3544" aria-hidden="true">
  <defs>
    <linearGradient id="bandFill" x1="0" y1="0" x2="1" y2="1">
      <stop offset="0" stop-color="#0a6fac"/><stop offset="1" stop-color="#0c63a0"/>
    </linearGradient>
  </defs>
  <path d="M0 1183 Q600 1321 1200 1183 L1200 1693 Q600 1871 0 1693 Z" fill="url(#bandFill)"/>
  <path d="M0 2174 Q600 2286 1200 2174 L1200 2587 Q600 2765 0 2587 Z" fill="url(#bandFill)"/>
  <path d="M0 3107 Q600 3237 1200 3107 L1200 3544 L0 3544 Z" fill="url(#bandFill)"/>
</svg>

<!-- top bar -->
<div class="abs topbar">
  <span class="abs welcome">Welcome Suds Haven !</span>
  <i class="abs dot" style="left:1029px"></i>
  <i class="abs dot" style="left:1056px"></i>
  <i class="abs dot" style="left:1088px"></i>
  <i class="abs dot" style="left:1125px"></i>
</div>

<header class="abs header"></header>
<div class="abs brand"><i></i>SUDS HAVEN</div>
<div class="abs nav-ring"></div>
<a class="abs nav active" style="left:392px">HOME</a>
<a class="abs nav" style="left:456px">ABOUT US</a>
<a class="abs nav" style="left:552px">SERVICES</a>
<a class="abs nav" style="left:643px">REVIEWS</a>
<a class="abs nav" style="left:733px">LOCATIONS</a>
<a class="abs nav" style="left:834px">CONATCT US</a>
<svg class="abs" style="left:934px;top:64px" width="19" height="19" viewBox="0 0 20 20"><circle cx="8" cy="8" r="6" fill="none" stroke="#0677BA" stroke-width="2.2"/><path d="M12.5 12.5 L18 18" stroke="#0677BA" stroke-width="2.4"/></svg>
<div class="abs phone-btn"><span class="ic"><svg width="20" height="20" viewBox="0 0 24 24"><path d="M6.6 10.8a15 15 0 0 0 6.6 6.6l2.2-2.2a1 1 0 0 1 1-.25 11.4 11.4 0 0 0 3.6.6 1 1 0 0 1 1 1V20a1 1 0 0 1-1 1A17 17 0 0 1 3 4a1 1 0 0 1 1-1h3.5a1 1 0 0 1 1 1c0 1.25.2 2.45.6 3.6a1 1 0 0 1-.25 1z" fill="#0677BA"/></svg></span>(404) 555-0148</div>

<!-- hero -->
<section class="abs hero"></section>
<div class="abs hero-arc"></div>
<h1 class="abs hero-title">One of Atlanta's First,<br>Finest, <em>&amp; Friendliest<br>Coin Laundries</em></h1>
<div class="abs offer"><b>»</b>GET BEST OFFER</div>
<div class="abs hero-ring"></div>
<div class="abs hero-photo" role="img" aria-label="Woman in a blue dress walking past a row of front-loading washers under a wall clock and shop sign"></div>

<!-- what we do -->
<h2 class="abs title" style="top:840px">WHAT WE DO ?</h2>
<div class="abs feature" style="left:47px;top:922px">
  <div class="ic"><svg width="56" height="56" viewBox="0 0 56 56" fill="none" stroke="#0054AA" stroke-width="2"><rect x="8" y="24" width="24" height="16" rx="2"/><path d="M32 28h8l6 6v6H32z"/><circle cx="16" cy="42" r="4"/><circle cx="40" cy="42" r="4"/><circle cx="32" cy="14" r="7"/><path d="M32 10v4l3 2"/></svg></div>
  <h3>Delivery Available</h3>
  <p>Lorem Ipsum is simply dummy text of the printing and typesetting industry. Lorem Ipsum</p>
</div>
<div class="abs feature" style="left:324px;top:922px">
  <div class="ic ring"><svg width="56" height="56" viewBox="0 0 56 56" fill="none" stroke="#0054AA" stroke-width="2"><circle cx="28" cy="28" r="14"/><circle cx="28" cy="28" r="20" stroke-dasharray="6 4"/><path d="M28 20v16M24 24h6a3 3 0 0 1 0 6h-4a3 3 0 0 0 0 6h6"/></svg></div>
  <h3>Cost Effective</h3>
  <p>Lorem Ipsum is simply dummy text of the printing and typesetting industry. Lorem Ipsum</p>
</div>
<div class="abs feature" style="left:598px;top:922px">
  <div class="ic"><svg width="56" height="56" viewBox="0 0 56 56" fill="none" stroke="#0054AA" stroke-width="2"><circle cx="28" cy="30" r="10"/><rect x="22" y="26" width="12" height="9" rx="1"/><circle cx="28" cy="10" r="4"/><circle cx="10" cy="26" r="4"/><circle cx="46" cy="26" r="4"/><circle cx="28" cy="48" r="4"/></svg></div>
  <h3>Commercial Accounts</h3>
  <p>Lorem Ipsum is simply dummy text of the printing and typesetting industry. Lorem Ipsum</p>
</div>
<div class="abs feature" style="left:874px;top:922px">
  <div class="ic"><svg width="56" height="56" viewBox="0 0 56 56" fill="none" stroke="#0054AA" stroke-width="2"><rect x="16" y="20" width="24" height="26" rx="2"/><circle cx="16" cy="14" r="5"/><circle cx="28" cy="12" r="5"/><circle cx="40" cy="14" r="5"/><path d="M21 33l5 5 9-10"/></svg></div>
  <h3>100 % Satisfaction</h3>
  <p>Lorem Ipsum is simply dummy text of the printing and typesetting industry. Lorem Ipsum</p>
</div>

<!-- services -->
<h2 class="abs title svc-title" style="top:1324px">WE PROVIDE SERVICES</h2>
<div class="abs drop down" style="left:161px;top:1444px"></div>
<div class="abs drop up" style="left:469px;top:1388px"></div>
<div class="abs drop down" style="left:777px;top:1444px"></div>

<div class="abs drop-body" style="left:161px;top:1428px">
  <div class="drop-photo" role="img" aria-label="Attendant hanging dry-cleaned shirts on a rack"></div>
  <h4>Dry&nbsp; Cleaning Drop Off</h4>
  <p>Lorem Ipsum is simply dummy text of the printing and typesetting</p>
</div>
<div class="abs drop-body" style="left:469px;top:1422px">
  <p>Lorem Ipsum is simply dummy text of the printing and typesetting</p>
  <h4 style="margin:2px 0 14px">Professional Laundry</h4>
  <div class="drop-photo inv" role="img" aria-label="Man loading laundry into a front-loading washer"></div>
</div>
<div class="abs drop-body" style="left:777px;top:1428px">
  <div class="drop-photo" role="img" aria-label="Hands folding fresh towels beside a washer"></div>
  <h4>Wash Dry Fold</h4>
  <p>Lorem Ipsum is simply dummy text of the printing and typesetting</p>
</div>

<!-- testimonials -->
<h2 class="abs title" style="top:1846px">WHAT OUR CLIENT SAY</h2>
<div class="abs client-photo" role="img" aria-label="Smiling customer holding a stack of folded laundry"></div>
<div class="abs quote-card"></div>
<div class="abs quote-badge">“</div>
<p class="abs quote-text">Lorem Ipsum is simply dummy text of the printing and typesetting industry. Lorem Ipsum has been the industry's standard dummy text ever since the 1500s,</p>
<div class="abs dots"><i></i><i></i><i></i></div>
<div class="abs model-photo" role="img" aria-label="Woman in a blue dress seated on a yellow chair"></div>

<!-- video -->
<h2 class="abs video-title">One of Atlanta's First, Finest, &amp;<br>Friendliest Coin Laundries</h2>
<p class="abs video-text">Lorem Ipsum is simply dummy text of the printing and typesetting industry. Lorem Ipsum has been the industry's standard dummy text ever since the 1500s.</p>
<a class="abs play" href="https://videohost-example.com/xq7Rm2bPz4k" aria-label="Play video"><span><svg width="16" height="18" viewBox="0 0 16 18"><path d="M2 1l13 8-13 8z" fill="#0677BA"/></svg></span></a>
<span class="abs watch">WATCH OUR VIDEO</span>

<!-- about -->
<h2 class="abs about-title">ABOUT US</h2>
<ul class="abs about-list">
  <li><span>Voted <em>"BEST COIN LAUNDRY"</em> - Multiple years</span></li>
  <li>One of Atlanta's First, Finest, &amp; Friendliest Coin Laundries</li>
  <li>The best Wash-Dry-Fold in town</li>
  <li>Cool - Comfortable - Clean</li>
  <li>Over 50 well maintained machines</li>
  <li>Commercial Accounts</li>
</ul>
<a class="abs more">VIEW MORE</a>
<div class="abs pic a" role="img" aria-label="Two friends chatting while waiting by the washers"></div>
<div class="abs pic b" role="img" aria-label="Woman using her phone in front of washers"></div>
<div class="abs pic c" role="img" aria-label="Row of clean front-loading washing machines"></div>
<div class="abs pic d" role="img" aria-label="Woman holding a stack of folded towels"></div>

<!-- footer -->
<div class="abs foot-brand"><i></i>SUDS HAVEN</div>
<div class="abs foot-social"><i></i><i></i><i></i></div>
<div class="abs foot-col" style="left:337px;top:3244px">
  <h5>Site Map</h5>
  <ul><li>- Home</li><li>- About Us</li><li>- Services</li><li>- Reviews</li><li>- Location</li><li>- Contact Us</li></ul>
</div>
<div class="abs foot-col" style="left:612px;top:3244px">
  <h5>Services</h5>
  <ul><li>- Dry cleaning drop</li><li>- Professional laundry services</li><li>- wash dry fold</li><li>- Self service laundry</li><li>- Commercial Accounts</li><li>- Oversize Machine</li></ul>
</div>
<div class="abs foot-col" style="left:888px;top:3244px"><h5>Contact Us</h5></div>
<div class="abs contact-row" style="top:3289px">
  <svg width="16" height="20" viewBox="0 0 16 20" fill="none" stroke="#fff" stroke-width="1.5"><path d="M8 19s6-7 6-11A6 6 0 0 0 2 8c0 4 6 11 6 11z"/><circle cx="8" cy="8" r="2.2"/></svg>
  <span>2210 Maple Row NE, #<br>118, Atlanta, GA 30309</span>
</div>
<div class="abs contact-row" style="top:3350px">
  <svg width="18" height="18" viewBox="0 0 24 24" fill="none" stroke="#fff" stroke-width="1.5"><path d="M6.6 10.8a15 15 0 0 0 6.6 6.6l2.2-2.2a1 1 0 0 1 1-.25 11.4 11.4 0 0 0 3.6.6 1 1 0 0 1 1 1V20a1 1 0 0 1-1 1A17 17 0 0 1 3 4a1 1 0 0 1 1-1h3.5a1 1 0 0 1 1 1c0 1.25.2 2.45.6 3.6a1 1 0 0 1-.25 1z"/></svg>
  <span style="font-size:14px">(404) 555-0148</span>
</div>
<div class="abs contact-row" style="top:3394px">
  <svg width="18" height="14" viewBox="0 0 18 14" fill="none" stroke="#fff" stroke-width="1.5"><rect x="1" y="1" width="16" height="12"/><path d="M1 1l8 7 8-7"/></svg>
  <span>hello@sudshavenatlanta-example.com</span>
</div>
<div class="abs copy">2021© Suds Haven - All Right Reserved.</div>

</body>
</html>
```